Pellham Grove Trust - New Website Designed

I need a site that looks like this http://www.quorlandgiving.org for boat donations. So please replace the cars with boats.

```html
<!DOCTYPE html>
<html lang="en">
<head>
<meta charset="utf-8">
<title>Pellham Grove Trust – Boat Donations</title>
<link rel="stylesheet" href="https://fonts.googleapis.com/css2?family=Mulish:wght@400;600;700&family=Open+Sans:wght@400;600;700&display=swap">
<style>
:root{
  --brand-blue:#0450a5;
  --nav-red:#d1343b;
  --nav-red-dark:#a8262c;
  --heading-red:#c9353b;
  --step-blue:#1c5aa3;
  --cta-dark:#222222;
  --submit-orange:#ef7a2c;
  --section-tint:#f4eff0;
  --text-body:#555555;
  --text-strong:#222222;
  --border:#cfcfcf;
  --footer:#444444;
  --white:#ffffff;
}
*{box-sizing:border-box;margin:0;padding:0}
html,body{width:1200px;height:2378px;overflow:hidden;background:var(--white)}
body{font-family:"Open Sans",Arial,sans-serif;color:var(--text-body);position:relative}
.section{position:absolute;left:0;width:1200px}

/* top bar */
.topbar{top:0;height:79px;background:var(--brand-blue)}
.site-name{position:absolute;left:130px;top:14px;font-family:"Mulish",Arial,sans-serif;font-weight:400;font-size:41px;color:var(--white);letter-spacing:.3px}
.phone{position:absolute;left:808px;top:26px;display:flex;align-items:center;gap:8px;font-family:"Mulish",Arial,sans-serif;font-weight:700;font-size:21px;color:var(--white)}
.social{position:absolute;top:23px;width:33px;height:33px;border:1.5px solid var(--white);border-radius:50%}
.social.first{left:985px}
.social.second{left:1033px}

/* nav */
.navbar{top:79px;height:40px;background:var(--nav-red)}
.nav-link{position:absolute;top:0;height:40px;line-height:40px;font-family:"Mulish",Arial,sans-serif;font-size:14px;color:var(--white)}
.nav-link.active{background:var(--nav-red-dark);padding:0 18px;left:132px}
.donate-cta{position:absolute;left:827px;top:2px;width:240px;height:38px;background:var(--cta-dark);color:var(--white);font-family:"Mulish",Arial,sans-serif;font-size:17px;display:flex;align-items:center;justify-content:center;gap:9px}

/* hero */
.hero{top:119px;height:494px}
.hero-visual{position:absolute;inset:0;background:linear-gradient(90deg,#8a7566 0%,#a99585 22%,#c8c2be 40%,#dcdcdc 62%,#e4e5e6 100%)}
.hero-headline{position:absolute;left:420px;top:70px;width:360px;text-align:center;font-family:"Mulish",Arial,sans-serif;font-weight:600;font-size:23px;line-height:29px;color:#333;text-transform:uppercase}
.pickup-form{position:absolute;left:788px;top:28px;width:279px;height:439px;background:var(--white);padding:10px 12px}
.form-title{font-family:"Mulish",Arial,sans-serif;font-weight:700;font-size:24px;color:var(--brand-blue);text-align:center;margin-bottom:6px}
.field{height:39px;border:1px solid var(--border);border-radius:3px;margin-bottom:9px;padding:0 11px;line-height:37px;font-size:11px;color:#9a9a9a}
.field-row{display:flex;gap:9px}
.field-row .field{flex:1;display:flex;justify-content:space-between;align-items:center}
.caret{width:0;height:0;border-left:4px solid transparent;border-right:4px solid transparent;border-top:5px solid #777}
.submit{height:39px;background:var(--submit-orange);color:var(--white);font-weight:600;font-size:14px;text-align:center;line-height:39px;border-radius:2px}

/* generic section text */
.section-title{position:absolute;left:0;width:1200px;text-align:center;font-family:"Mulish",Arial,sans-serif;font-weight:400;font-size:30px;color:var(--heading-red)}
.section-copy{position:absolute;left:135px;width:930px;text-align:center;font-size:11px;line-height:20.5px;color:var(--text-body)}

.welcome{top:613px;height:279px;background:var(--section-tint)}
.why{top:892px;height:387px;background:var(--white)}
.benefit{position:absolute;display:flex;align-items:center;gap:14px;font-family:"Open Sans",Arial,sans-serif;font-weight:600;font-size:16px;color:var(--text-strong)}
.benefit svg{flex:none}

.how{top:1279px;height:456px;background:var(--section-tint)}
.step{position:absolute;top:125px;width:300px;text-align:center}
.step-photo{width:158px;height:158px;border-radius:50%;border:7px solid var(--white);margin:0 auto;box-shadow:0 0 0 1px #ececec}
.step-title{margin-top:10px;font-family:"Mulish",Arial,sans-serif;font-size:19px;color:var(--step-blue)}
.step-copy{margin-top:4px;font-size:10.5px;line-height:16.5px;color:var(--text-body);padding:0 8px}

.faq{top:1735px;height:547px;background:var(--white)}
.faq-item{position:absolute;left:132px;width:935px;height:48px;border:1px solid var(--border);display:flex;align-items:center;justify-content:space-between;padding:0 15px;font-family:"Mulish",Arial,sans-serif;font-size:16px;color:var(--text-strong)}

.footer{top:2282px;height:96px;background:var(--footer);text-align:center;font-family:"Mulish",Arial,sans-serif;color:#e6e6e6}
.footer-links{position:absolute;top:24px;width:1200px;font-size:11px}
.footer-links span{margin:0 6px}
.copyright{position:absolute;top:51px;width:1200px;font-size:11px}
</style>
</head>
<body>

<header class="section topbar">
  <div class="site-name">Pellham Grove Trust</div>
  <div class="phone">
    <svg width="16" height="16" viewBox="0 0 24 24" aria-hidden="true"><path fill="#fff" d="M6.6 10.8a15.1 15.1 0 0 0 6.6 6.6l2.2-2.2c.3-.3.7-.4 1-.2 1.1.4 2.3.6 3.6.6.6 0 1 .4 1 1V20c0 .6-.4 1-1 1A17 17 0 0 1 3 4c0-.6.4-1 1-1h3.5c.6 0 1 .4 1 1 0 1.3.2 2.5.6 3.6.1.3 0 .7-.2 1z"/></svg>
    555 014 2270
  </div>
  <div class="social first"></div>
  <div class="social second"></div>
</header>

<nav class="section navbar">
  <span class="nav-link active">Home</span>
  <span class="nav-link" style="left:223px">About</span>
  <span class="nav-link" style="left:298px">Why donate</span>
  <span class="nav-link" style="left:409px">How to donate</span>
  <span class="nav-link" style="left:537px">FAQ</span>
  <span class="nav-link" style="left:599px">Support</span>
  <div class="donate-cta">
    <svg width="16" height="16" viewBox="0 0 16 16" aria-hidden="true"><circle cx="8" cy="8" r="8" fill="#fff"/><path d="M4 8h6M8 5l3 3-3 3" stroke="#222" stroke-width="2" fill="none"/></svg>
    Donate Your Boat Now
  </div>
</nav>

<section class="section hero">
  <div class="hero-visual" role="img" aria-label="Photo of a smiling soldier in camouflage hugging his young daughter, with a white motorboat on calm water behind them"></div>
  <h1 class="hero-headline">Maecenas efficitur diam ut orci scelerisque</h1>
  <form class="pickup-form">
    <div class="form-title">Donation Pickup Form</div>
    <div class="field">First Name</div>
    <div class="field">Last Name</div>
    <div class="field">Zip Code</div>
    <div class="field">Day Phone</div>
    <div class="field">Email Address</div>
    <div class="field-row">
      <div class="field">Choose Year <span class="caret"></span></div>
      <div class="field">Choose Make <span class="caret"></span></div>
    </div>
    <div class="field">Model of Boat</div>
    <div class="submit">SUBMIT</div>
  </form>
</section>

<section class="section welcome">
  <h2 class="section-title" style="top:74px">Welcome to Pellham Grove Trust</h2>
  <p class="section-copy" style="top:118px">Every boat given to our trust helps a veteran family find steady footing again. We collect sailboats, motorboats, pontoons and personal watercraft in almost any condition, running or not. Our volunteers handle the paperwork, arrange a free tow at a time that suits you, and send a receipt for your records. Proceeds from each sale fund housing support, job training, counselling and transport for men and women who served. Your donation is simple to make, fully tax deductible, and goes straight to programmes that change lives in local communities across the country every single year.</p>
</section>

<section class="section why">
  <h2 class="section-title" style="top:72px">Why Donate?</h2>
  <p class="section-copy" style="top:114px">Donating a boat you no longer use is one of the easiest ways to give back. There is no need to pay for repairs, advertising or storage, and no strangers coming to your door. We take care of every step, from the first call to the final pick up, so you can support veterans with almost no effort at all and a clear conscience.</p>

  <div class="benefit" style="left:195px;top:204px">
    <svg width="14" height="16" viewBox="0 0 14 16" aria-hidden="true"><path d="M1 1h8l4 4v10H1z" fill="none" stroke="#222" stroke-width="1.6"/><path d="M4 8h6M4 11h6" stroke="#222" stroke-width="1.4"/></svg>
    Aliquam interdum tortor erat</div>
  <div class="benefit" style="left:195px;top:243px">
    <svg width="16" height="14" viewBox="0 0 16 14" aria-hidden="true"><rect x="0" y="2" width="10" height="8" fill="#222"/><path d="M10 5h3l3 3v2h-6z" fill="#222"/><circle cx="4" cy="11.5" r="2" fill="#222"/><circle cx="12.5" cy="11.5" r="2" fill="#222"/></svg>
    Praesent sollicitudin, justo quis faucibus</div>
  <div class="benefit" style="left:195px;top:283px">
    <svg width="15" height="15" viewBox="0 0 15 15" aria-hidden="true"><rect x="5" y="1" width="8" height="5" transform="rotate(45 9 3.5)" fill="#222"/><path d="M7 7l-6 6" stroke="#222" stroke-width="2.4"/></svg>
    Quisque venenatis viverra leo</div>

  <div class="benefit" style="left:658px;top:204px">
    <svg width="16" height="16" viewBox="0 0 16 16" aria-hidden="true"><path d="M8 0l8 4H0z" fill="#222"/><path d="M2 5v7M6 5v7M10 5v7M14 5v7" stroke="#222" stroke-width="2"/><rect x="0" y="13" width="16" height="3" fill="#222"/></svg>
    Aenean mattis volutpat massa</div>
  <div class="benefit" style="left:658px;top:243px">
    <svg width="13" height="16" viewBox="0 0 13 16" aria-hidden="true"><rect x=".8" y=".8" width="11.4" height="14.4" fill="none" stroke="#222" stroke-width="1.6"/><rect x="3" y="3" width="7" height="3" fill="#222"/><path d="M3 9h2M6 9h2M9 9h1M3 12h2M6 12h2M9 12h1" stroke="#222" stroke-width="1.6"/></svg>
    Proin efficitur, sem nec imperdiet rhoncus</div>
  <div class="benefit" style="left:658px;top:283px">
    <svg width="16" height="16" viewBox="0 0 16 16" aria-hidden="true"><circle cx="8" cy="8" r="6.8" fill="none" stroke="#222" stroke-width="1.8"/><path d="M5 8.2l2 2 4-4" stroke="#222" stroke-width="1.8" fill="none"/></svg>
    Pellentesque risus dolor, tristique vel</div>
</section>

<section class="section how">
  <h2 class="section-title" style="top:72px">How to Donate?</h2>
  <div class="step" style="left:124px">
    <div class="step-photo" role="img" aria-label="Photo of a man working on a laptop on the deck of a boat" style="background:linear-gradient(160deg,#e9eef3,#a9b6c6 55%,#6f86a6)"></div>
    <div class="step-title">Call or Fill Form</div>
    <p class="step-copy">Reach our team by phone or send the short form above. We reply within one working day to confirm details.</p>
  </div>
  <div class="step" style="left:449px">
    <div class="step-photo" role="img" aria-label="Photo of a white motorboat being towed on a trailer" style="background:linear-gradient(180deg,#4c5a3c,#8a8f88 50%,#3c3d3a)"></div>
    <div class="step-title">We Tow Boat Free</div>
    <p class="step-copy">Our driver collects your boat and trailer at no cost, wherever it is moored or stored.</p>
  </div>
  <div class="step" style="left:774px">
    <div class="step-photo" role="img" aria-label="Photo of folded paper bills resting on a table" style="background:linear-gradient(180deg,#dfe4e8,#cfcac6 55%,#9c7f6c)"></div>
    <div class="step-title">Tax Write Off</div>
    <p class="step-copy">After the sale we mail a receipt you can use to claim a deduction on your tax return.</p>
  </div>
</section>

<section class="section faq">
  <h2 class="section-title" style="top:70px">FAQs</h2>
  <div class="faq-item" style="top:138px">Suspendisse feugiat purus metus, nec interdum elit dignissim eget?<svg width="14" height="14" viewBox="0 0 14 14" aria-hidden="true"><circle cx="7" cy="7" r="6" fill="none" stroke="#444" stroke-width="1.4"/><path d="M7 3.5v6M4.5 7l2.5 2.5L9.5 7" stroke="#444" stroke-width="1.4" fill="none"/></svg></div>
  <div class="faq-item" style="top:193px">Pellentesque habitant morbi tristique senectus et netus et malesuada fames?<svg width="14" height="14" viewBox="0 0 14 14" aria-hidden="true"><circle cx="7" cy="7" r="6" fill="none" stroke="#444" stroke-width="1.4"/><path d="M7 3.5v6M4.5 7l2.5 2.5L9.5 7" stroke="#444" stroke-width="1.4" fill="none"/></svg></div>
  <div class="faq-item" style="top:249px">Etiam fermentum ipsum ullamcorper ullamcorper?<svg width="14" height="14" viewBox="0 0 14 14" aria-hidden="true"><circle cx="7" cy="7" r="6" fill="none" stroke="#444" stroke-width="1.4"/><path d="M7 3.5v6M4.5 7l2.5 2.5L9.5 7" stroke="#444" stroke-width="1.4" fill="none"/></svg></div>
  <div class="faq-item" style="top:304px">Nulla sed dolor auctor, porta ex in, laoreet odio?<svg width="14" height="14" viewBox="0 0 14 14" aria-hidden="true"><circle cx="7" cy="7" r="6" fill="none" stroke="#444" stroke-width="1.4"/><path d="M7 3.5v6M4.5 7l2.5 2.5L9.5 7" stroke="#444" stroke-width="1.4" fill="none"/></svg></div>
  <div class="faq-item" style="top:360px">Praesent blandit, neque at porta sodales, ex diam tempus mi, eu fringilla odio leo at diam?<svg width="14" height="14" viewBox="0 0 14 14" aria-hidden="true"><circle cx="7" cy="7" r="6" fill="none" stroke="#444" stroke-width="1.4"/><path d="M7 3.5v6M4.5 7l2.5 2.5L9.5 7" stroke="#444" stroke-width="1.4" fill="none"/></svg></div>
  <div class="faq-item" style="top:415px">Praesent scelerisque fermentum mauris ut posuere?<svg width="14" height="14" viewBox="0 0 14 14" aria-hidden="true"><circle cx="7" cy="7" r="6" fill="none" stroke="#444" stroke-width="1.4"/><path d="M7 3.5v6M4.5 7l2.5 2.5L9.5 7" stroke="#444" stroke-width="1.4" fill="none"/></svg></div>
</section>

<footer class="section footer">
  <div class="footer-links">Home<span>|</span>About<span>|</span>Why donate<span>|</span>How to donate<span>|</span>FAQ<span>|</span>Support</div>
  <div class="copyright">Copyright &nbsp;©&nbsp; 2017 &nbsp; Pellham Grove Trust. &nbsp; All rights reserved.</div>
</footer>

</body>
</html>
```